Personal training and nutrition business needs business card design

We need a business card that outlays our services and invites potential customers to join our team and take the first step to a healthier and more enjoyable life. We cater for any level of fitness and specialize in weight loss and conditioning, strength training, muscle gain and strength endurance. Whether you are just starting off or need some help getting to the next level of your journey we are here to get the job done.
We specialize in one on one or one on two personal training sessions and each program will be custom made to suit individual fitness goals of our clients

```html
<!DOCTYPE html>
<html lang="en">
<head>
<meta charset="utf-8">
<title>Stride &amp; Tempo – Business Card</title>
<link rel="stylesheet" href="https://fonts.googleapis.com/css2?family=Rubik:wght@800&family=Oswald:wght@500&family=Roboto:wght@400&family=Saira+Condensed:wght@600&display=swap">
<style>
  :root {
    --bg: #2b2b2b;
    --card: #1c1c1e;
    --emboss: #3b3b3e;
    --purple: #9a55a8;
    --purple-deep: #6a4495;
    --purple-light: #a65aa6;
    --white: #f2f2f2;
    --text: #e6e6e6;
  }
  * { margin: 0; padding: 0; box-sizing: border-box; }
  html, body {
    width: 1200px; height: 1138px; overflow: hidden;
    background: var(--bg);
  }
  .stage { position: relative; width: 1200px; height: 1138px; }
  .card {
    position: absolute;
    left: 275px; width: 620px; height: 374px;
    background: var(--card);
    border-radius: 14px;
    overflow: hidden;
    box-shadow: 0 10px 24px rgba(0,0,0,.35);
  }
  .card--front { top: 186px; }
  .card--back { top: 608px; }

  /* Front */
  .front-brand {
    position: absolute; left: 0; right: 0; top: 200px;
    display: flex; justify-content: center; align-items: center; gap: 14px;
  }
  .front-brand__mark { width: 26px; height: 26px; background: var(--emboss); }
  .front-brand__name {
    font-family: "Rubik", sans-serif; font-weight: 800;
    font-size: 40px; letter-spacing: 1px; color: var(--emboss);
    text-transform: uppercase;
  }
  .tagline {
    font-family: "Oswald", sans-serif; font-weight: 500;
    color: var(--purple); text-transform: uppercase; letter-spacing: 1.4px;
  }
  .front-tagline {
    position: absolute; left: 0; right: 0; top: 333px;
    text-align: center; font-size: 13px;
  }

  /* Back */
  .back-block {
    position: absolute; left: 36px; top: 30px; width: 250px; height: 310px;
    background: linear-gradient(135deg, var(--purple-deep), var(--purple-light));
    border-radius: 6px;
  }
  .back-notch {
    position: absolute; right: -22px; top: 150px;
    width: 44px; height: 62px; border-radius: 50%;
    background: var(--purple-light);
  }
  .back-info {
    position: absolute; right: 40px; top: 32px; width: 290px;
    text-align: right;
  }
  .back-brand {
    font-family: "Rubik", sans-serif; font-weight: 800;
    font-size: 30px; line-height: 32px; color: var(--white);
    text-transform: uppercase; letter-spacing: 1px;
  }
  .back-tagline { font-size: 8.5px; margin-top: 6px; letter-spacing: .9px; }
  .person__name {
    font-family: "Saira Condensed", sans-serif; font-weight: 600;
    font-size: 27px; color: var(--purple); margin-top: 40px; line-height: 30px;
  }
  .person__role {
    font-family: "Roboto", sans-serif; font-size: 16px; color: var(--text);
    margin-top: 2px;
  }
  .contact { list-style: none; margin-top: 26px; }
  .contact__item {
    display: flex; justify-content: flex-end; align-items: center; gap: 12px;
    font-family: "Roboto", sans-serif; font-size: 16px; color: var(--text);
    height: 24px; white-space: nowrap;
  }
  .contact__icon { width: 15px; height: 15px; fill: var(--purple); flex: none; }
  .address {
    font-family: "Roboto", sans-serif; font-size: 16px; color: var(--text);
    margin-top: 10px; white-space: nowrap;
  }
</style>
</head>
<body>
<main class="stage">
  <section class="card card--front" aria-label="Card front">
    <div class="front-brand">
      <span class="front-brand__mark"></span>
      <span class="front-brand__name">Stride &amp; Tempo</span>
    </div>
    <p class="tagline front-tagline">Personal Training.&nbsp; Nutrition. Motivation</p>
  </section>

  <section class="card card--back" aria-label="Card back">
    <div class="back-block"></div>
    <div class="back-notch"></div>
    <div class="back-info">
      <h1 class="back-brand">Stride<br>&amp; Tempo</h1>
      <p class="tagline back-tagline">Personal Training.&nbsp; Nutrition. Motivation</p>
      <h2 class="person__name">Marcus Vale</h2>
      <p class="person__role">Personal Trainer</p>
      <ul class="contact">
        <li class="contact__item">+1 (555) 204-7318
          <svg class="contact__icon" viewBox="0 0 16 16"><path d="M2 5c0-2 3-3 6-3s6 1 6 3v1h-3V5H5v1H2z M4 7h8l2 6H2z"/></svg>
        </li>
        <li class="contact__item">marcus@strideandtempo.com
          <svg class="contact__icon" viewBox="0 0 16 16"><path d="M1 3h14v10H1z M2 4l6 5 6-5" fill="none" stroke="#9a55a8" stroke-width="1.6"/></svg>
        </li>
        <li class="contact__item">www.strideandtempo.com
          <svg class="contact__icon" viewBox="0 0 16 16"><g fill="none" stroke="#9a55a8" stroke-width="1.3"><circle cx="8" cy="8" r="6.5"/><ellipse cx="8" cy="8" rx="3" ry="6.5"/><path d="M1.5 8h13M3 4.5h10M3 11.5h10"/></g></svg>
        </li>
      </ul>
      <p class="address">418 Willow Bend Road Austin 78701</p>
    </div>
  </section>
</main>
</body>
</html>
```